Brightmill Data Works

Our company is about IT hardwares and IT solutions. IT hardware such as PC, RAMS, storage and servers. IT solutions such as project management, BA. We are also selling new technology too.

Target Market(s)

Consumer, Small to Medium Business, Corporate

Requirements
Must have
• The business card must have the following:
• Name:
• Title:
• Contact Number:
• Email address:
• Website:
• Color: Must match the logo color upgrade

```html
<!DOCTYPE html>
<html lang="en">
<head>
<meta charset="UTF-8">
<title>Brightmill Data Works – Business Card</title>
<link href="https://fonts.googleapis.com/css2?family=Work+Sans:wght@400;500;700&display=swap" rel="stylesheet">
<style>
  :root {
    --backdrop: #1a1a1a;
    --card: #232323;
    --card-edge: #2b2b2b;
    --amber: #e39a33;
    --white: #f5f5f5;
    --muted: #d9d9d9;
  }
  * { box-sizing: border-box; margin: 0; padding: 0; }
  html, body {
    width: 1200px; height: 900px; overflow: hidden;
    background: var(--backdrop);
    font-family: "Work Sans", sans-serif;
  }
  .stage {
    width: 1200px; height: 900px;
    display: flex; flex-direction: column; align-items: center; justify-content: center;
    gap: 36px;
  }
  .card {
    position: relative;
    width: 700px; height: 400px;
    background: linear-gradient(135deg, var(--card) 0%, var(--card-edge) 100%);
    border-bottom: 6px solid var(--amber);
    box-shadow: 0 16px 36px rgba(0,0,0,0.55);
  }
  .brand {
    display: flex; align-items: center; gap: 14px;
  }
  .brand-mark {
    width: 22px; height: 22px; background: var(--amber); flex: none;
  }
  .brand-name {
    font-weight: 700; color: var(--white);
    text-transform: uppercase; letter-spacing: 0.5px; line-height: 1;
  }
  /* Front */
  .card-front {
    display: flex; align-items: center; justify-content: center;
  }
  .card-front .brand-name { font-size: 40px; }
  /* Back */
  .card-back {
    display: flex; align-items: center; padding: 0 44px;
  }
  .card-back .brand { width: 300px; }
  .card-back .brand-name { font-size: 26px; }
  .divider {
    width: 2px; height: 210px; background: var(--white); margin: 0 34px 0 18px;
  }
  .contact { color: var(--white); }
  .person-name {
    font-size: 26px; font-weight: 500; color: var(--amber);
    text-transform: uppercase; letter-spacing: 0.5px;
  }
  .person-title { font-size: 17px; margin-bottom: 16px; }
  .address { font-size: 17px; line-height: 1.35; margin-bottom: 14px; }
  .contact-line {
    display: flex; align-items: center; gap: 10px;
    font-size: 18px; line-height: 1.5;
  }
  .contact-line svg { width: 14px; height: 14px; flex: none; }
  .domain { color: var(--amber); }
</style>
</head>
<body>
<main class="stage">
  <section class="card card-front">
    <div class="brand">
      <span class="brand-mark"></span>
      <span class="brand-name">Brightmill Data Works</span>
    </div>
  </section>

  <section class="card card-back">
    <div class="brand">
      <span class="brand-mark"></span>
      <span class="brand-name">Brightmill Data Works</span>
    </div>
    <div class="divider"></div>
    <div class="contact">
      <p class="person-name">Daniel Reyes</p>
      <p class="person-title">Director</p>
      <p class="address">2280 Orchard Lane<br>Fairview, CA 95012-4410</p>
      <p class="contact-line">
        <svg viewBox="0 0 16 16" aria-hidden="true"><path d="M3 1.5l3 .5 1 3-1.8 1.3a9 9 0 0 0 4.5 4.5L11 9l3 1 .5 3-1.5 1.5C7 14.5 1.5 9 1.5 3z" fill="none" stroke="var(--amber)" stroke-width="1.5"/></svg>
        555-014-2270
      </p>
      <p class="contact-line">
        <svg viewBox="0 0 16 16" aria-hidden="true"><rect x="1.5" y="3.5" width="13" height="9" fill="none" stroke="var(--amber)" stroke-width="1.5"/><path d="M1.5 3.5L8 9l6.5-5.5" fill="none" stroke="var(--amber)" stroke-width="1.5"/></svg>
        info@brightmilldata.com
      </p>
      <p class="contact-line">
        <svg viewBox="0 0 16 16" aria-hidden="true"><circle cx="8" cy="8" r="6.5" fill="none" stroke="var(--amber)" stroke-width="1.5"/><path d="M1.5 8h13M8 1.5c-3 3.5-3 9.5 0 13M8 1.5c3 3.5 3 9.5 0 13" fill="none" stroke="var(--amber)" stroke-width="1.2"/></svg>
        <span>www.<span class="domain">brightmilldata</span>.com</span>
      </p>
    </div>
  </section>
</main>
</body>
</html>
```